We are a recruitment company based in Norwich/Cambridge England.
I have included our company logo which we want to remain the same.

What we are looking for is a new creative Business card which will really stand out!!

Contact Information for Business Card

Harriet Dunmore
email: Harriet@plavex.co.uk
Address: Brackwell House
Fenmoor Enterprise Park
Partridge Way
Norwich
QB9 3KX
Tel:01632 960418

```html
<!DOCTYPE html>
<html lang="en">
<head>
<meta charset="utf-8">
<title>Plavex Business Card</title>
<link rel="stylesheet" href="https://fonts.googleapis.com/css2?family=Roboto:wght@400;500;700&display=swap">
<style>
  :root {
    --backdrop: #2b2b2b;
    --card-white: #f7f7f7;
    --brand-green: #8cc541;
    --brand-grey: #8a878b;
    --text-white: #ffffff;
    --shadow: rgba(0, 0, 0, 0.45);
  }
  * { margin: 0; padding: 0; box-sizing: border-box; }
  html, body {
    width: 1200px; height: 960px; overflow: hidden;
    background: var(--backdrop);
    font-family: "Roboto", Arial, sans-serif;
  }
  .canvas { position: relative; width: 1200px; height: 960px; }

  .card {
    position: absolute; left: 320px; width: 600px; height: 342px;
    box-shadow: 0 6px 14px var(--shadow);
    overflow: hidden;
  }

  /* Front */
  .card-front { top: 108px; background: var(--card-white); }
  .brand {
    position: absolute; top: 88px; left: 0; width: 100%;
    display: flex; flex-direction: column; align-items: center;
  }
  .brand-row { display: flex; align-items: center; gap: 14px; }
  .brand-dot { width: 30px; height: 30px; border-radius: 50%; background: var(--brand-green); }
  .brand-name {
    font-size: 46px; font-weight: 500; color: var(--brand-grey);
    line-height: 1; letter-spacing: 0.5px;
  }
  .brand-tagline {
    margin-top: 6px; margin-left: 44px;
    font-size: 9px; letter-spacing: 2.4px; color: var(--brand-grey);
  }

  .details-band {
    position: absolute; left: 0; bottom: 0; width: 100%; height: 132px;
    display: flex;
  }
  .identity {
    width: 303px; background: var(--brand-green); color: var(--text-white);
    padding: 24px 0 0 29px;
  }
  .identity-name { font-size: 19px; font-weight: 700; letter-spacing: 0.2px; }
  .identity-role { font-size: 14px; font-weight: 500; margin-top: 3px; }
  .identity-address { font-size: 13.5px; line-height: 19px; margin-top: 10px; }
  .divider { width: 2px; background: var(--card-white); }
  .contacts {
    flex: 1; background: var(--brand-grey); color: var(--text-white);
    padding: 20px 20px 0 0;
    list-style: none;
  }
  .contact-item {
    display: flex; justify-content: flex-end; align-items: center; gap: 8px;
    font-size: 13.5px; line-height: 19px;
  }
  .contact-icon { width: 13px; height: 13px; fill: var(--text-white); }

  /* Back */
  .card-back { top: 493px; background: var(--brand-green); }
  .back-brand {
    position: absolute; top: 120px; left: 0; width: 100%;
    display: flex; justify-content: center; align-items: center; gap: 16px;
  }
  .back-dot { width: 40px; height: 40px; border-radius: 50%; background: var(--text-white); }
  .back-name { font-size: 58px; font-weight: 500; color: var(--text-white); line-height: 1; }
  .back-web {
    position: absolute; bottom: 26px; width: 100%; text-align: center;
    font-size: 13px; letter-spacing: 5px; color: var(--text-white);
  }
</style>
</head>
<body>
<main class="canvas">
  <section class="card card-front" aria-label="Business card front">
    <div class="brand">
      <div class="brand-row">
        <span class="brand-dot"></span>
        <span class="brand-name">Plavex</span>
      </div>
      <span class="brand-tagline">Technology Recruitment</span>
    </div>
    <div class="details-band">
      <div class="identity">
        <p class="identity-name">HARRIET DUNMORE</p>
        <p class="identity-role">CEO/FOUNDER</p>
        <p class="identity-address">Brackwell House<br>Norwich QB9 3KX</p>
      </div>
      <div class="divider"></div>
      <ul class="contacts">
        <li class="contact-item">01632 960418
          <svg class="contact-icon" viewBox="0 0 16 16"><path d="M3.6 1.2l2.3 2.6-1.3 1.9c.9 2 2.6 3.8 4.7 4.7l1.9-1.3 2.6 2.3-1.1 2.4C7.3 14 2 8.7 1.2 2.3z"/></svg>
        </li>
        <li class="contact-item">07700 900317
          <svg class="contact-icon" viewBox="0 0 16 16"><path d="M4 1h8v14H4zM5.5 2.5v9h5v-9zM7.2 12.6h1.6v1.2H7.2z" fill-rule="evenodd"/></svg>
        </li>
        <li class="contact-item">01632 960522
          <svg class="contact-icon" viewBox="0 0 16 16"><path d="M4 1h8v4H4zM1 6h14v6h-2v3H3v-3H1zM4.5 10v3.5h7V10z" fill-rule="evenodd"/></svg>
        </li>
        <li class="contact-item">Harriet@plavex.co.uk
          <svg class="contact-icon" viewBox="0 0 16 16"><path d="M1 3h14v10H1zM2.5 4.5L8 8.5l5.5-4z" fill-rule="evenodd"/></svg>
        </li>
        <li class="contact-item">www.plavex.co.uk
          <svg class="contact-icon" viewBox="0 0 16 16"><circle cx="8" cy="8" r="7"/><path d="M1 8h14M8 1c-3 3.5-3 10.5 0 14M8 1c3 3.5 3 10.5 0 14" stroke="#8a878b" stroke-width="1" fill="none"/></svg>
        </li>
      </ul>
    </div>
  </section>

  <section class="card card-back" aria-label="Business card back">
    <div class="back-brand">
      <span class="back-dot"></span>
      <span class="back-name">Plavex</span>
    </div>
    <p class="back-web">www.plavex.co.uk</p>
  </section>
</main>
</body>
</html>
```